Dental Medical History Form - Content provided

Design a medical history form for a dental practice. Content is provided so all that is needed is the formatting to make it look great and easy to read.

"Patient Information" to include all information contained in top portion of the "Patient Medical History Form" docx file.

"Medical History" should follow the formatting and content of the "Exact Medical History" file as this is what the entry fields look like in our practice software and so we would like it to match.

1st page - Patient info, allergies, medications, antibiotics, joint replacement, pregnancy.

2nd page - Do you have, or have you had, any of the following? . . . . . . .
Updates

Target Market(s)

All ages but must be clear enough for elderly to read. Use as much space as possible to keep font size bigger yet keep to two pages

Industry/Entity Type

Dental

Font styles to use
Sans Serif

Requirements
Must have
• All content provided
• Our logo at the top (file provided)
• Century Gothic Font
• Limit to two pages

```html
<!DOCTYPE html>
<html lang="en">
<head>
<meta charset="utf-8">
<title>Harbour Dental – Confidential Medical History</title>
<link href="https://fonts.googleapis.com/css2?family=Questrial&display=swap" rel="stylesheet">
<style>
:root{
  --bg:#e6e5e3;
  --paper:#ffffff;
  --ink:#1d1d1f;
  --logo:#77787b;
  --rule:#3a3a3a;
  --box:#6b6b6b;
  --band-1:#5d5e62;
  --band-2:#a0a0a2;
  --band-3:#c9c1b9;
  --band-4:#dcdcdc;
}
*{box-sizing:border-box;margin:0;padding:0}
html,body{width:1200px;height:927px;overflow:hidden}
body{background:var(--bg);font-family:"Questrial","Century Gothic",sans-serif;color:var(--ink);position:relative}
.page{position:absolute;width:476px;height:672px;background:var(--paper)}
.page--one{left:94px;top:70px}
.page--two{left:623px;top:162px}
.band{position:absolute;left:0;right:0;height:6px;display:flex}
.band--top{top:0}.band--bottom{bottom:0}
.band span{flex:1}
.band span:nth-child(1){background:var(--band-1)}
.band span:nth-child(2){background:var(--band-2)}
.band span:nth-child(3){background:var(--band-3)}
.band span:nth-child(4){background:var(--band-4)}
.brand{position:absolute;display:flex;align-items:center;gap:6px;color:var(--logo);font-size:25px;letter-spacing:.3px;line-height:1}
.brand__dot{width:9px;height:9px;border-radius:50%;background:var(--logo)}
.practice{position:absolute;right:29px;top:29px;text-align:right;font-size:7.4px;line-height:9.6px}
.title{position:absolute;left:0;right:0;top:104px;text-align:center;font-size:14.5px;font-weight:700;letter-spacing:.2px}
.a{position:absolute;font-size:8.8px;line-height:1;white-space:nowrap}
.h{font-weight:700}
.sm{font-size:7.3px}
.tiny{font-size:5.6px;font-style:italic}
.field{position:absolute;display:flex;align-items:flex-end;font-size:8.8px;line-height:1;white-space:nowrap}
.field .line{flex:1;border-bottom:.8px solid var(--rule);margin-left:1px;height:8px}
.rule{position:absolute;border-bottom:.8px solid var(--rule);height:0}
.box{display:inline-block;width:8px;height:8px;border:.8px solid var(--box);vertical-align:-1px}
.abox{position:absolute;width:8px;height:8px;border:.8px solid var(--box)}
.tick{display:inline-block;vertical-align:-3px}
.turn{position:absolute;right:41px;top:631px;font-size:8.8px;font-weight:700;font-style:italic}
.section{position:absolute;font-size:8.2px;line-height:10.5px}
.section__head{font-weight:700}
.q{display:grid;height:10.5px;align-items:center;white-space:nowrap}
.section--left .q{grid-template-columns:171px 20px 16px 16px 12px}
.section--right .q{grid-template-columns:120px 20px 16px 16px 12px}
.q .box{width:9px;height:9px}
.q--tall{height:21px;align-items:start}
.q--tall .label{line-height:10.5px}
.q--tall > span:not(.label){margin-top:1px}
.intro{position:absolute;left:23px;top:78px;font-size:9.4px}
.footer{position:absolute;left:0;right:0;top:626px;text-align:center;font-size:6.4px;font-style:italic;line-height:9.6px}
</style>
</head>
<body>

<section class="page page--one" aria-label="Page one: patient information">
  <div class="band band--top"><span></span><span></span><span></span><span></span></div>

  <div class="brand" style="left:29px;top:32px"><span>harbour dental</span><span class="brand__dot"></span></div>
  <address class="practice" style="font-style:normal">Harbour Dental<br>Suite 4, 18 Marlow Street<br>Kenton NSW 2261<br>(02) 4000 1234</address>

  <h1 class="title">CONFIDENTIAL MEDICAL HISTORY</h1>

  <!-- patient details -->
  <div class="field" style="left:30px;top:132px;width:210px">Name:<span class="line"></span></div>
  <span class="a tiny" style="left:66px;top:148px">Title</span>
  <span class="a tiny" style="left:110px;top:148px">First</span>
  <span class="a tiny" style="left:144px;top:148px">Middle</span>
  <span class="a tiny" style="left:197px;top:148px">Last</span>
  <div class="field" style="left:32px;top:157px;width:208px">Address:<span class="line"></span></div>
  <div class="field" style="left:30px;top:170px;width:153px">DOB:<span class="line"></span></div>
  <div class="field" style="left:30px;top:183px;width:210px">Email Address:<span class="line"></span></div>
  <div class="field" style="left:30px;top:196px;width:210px">Phone Number(s):<span class="line"></span></div>
  <span class="a tiny" style="left:121px;top:212px">Mobile</span>
  <span class="a tiny" style="left:163px;top:212px">Work</span>
  <span class="a tiny" style="left:202px;top:212px">Home</span>

  <span class="a h" style="left:30px;top:236px">Emergency Contact Person:</span>
  <div class="field" style="left:30px;top:250px;width:205px">Name:<span class="line"></span></div>
  <div class="field" style="left:30px;top:263px;width:205px">Relationship:<span class="line"></span></div>
  <div class="field" style="left:30px;top:277px;width:205px">Phone number:<span class="line"></span></div>

  <!-- practitioner & fund -->
  <span class="a h" style="left:250px;top:137px">General Practitioner:</span>
  <div class="field" style="left:250px;top:149px;width:198px">Name:<span class="line"></span></div>
  <div class="field" style="left:250px;top:161px;width:198px">Practice Name:<span class="line"></span></div>
  <div class="field" style="left:250px;top:173px;width:177px">Phone Number:<span class="line"></span></div>
  <span class="a" style="left:250px;top:197px">Do you have a health fund with dental cover?</span>
  <span class="a" style="left:314px;top:209px"><span class="box"></span> Yes &nbsp;or <span class="box"></span>No</span>
  <div class="field" style="left:250px;top:221px;width:198px">If so, what is the name of the fund?<span class="line"></span></div>
  <div class="field" style="left:250px;top:233px;width:195px">Fund Number?<span class="line"></span></div>
  <span class="a" style="left:250px;top:245px">Priority Number on card: 0 &nbsp;1 &nbsp;2 &nbsp;3 &nbsp;4 &nbsp;&nbsp;5</span>
  <div class="field" style="left:250px;top:269px;width:186px">Occupation:<span class="line"></span></div>
  <div class="field" style="left:250px;top:281px;width:178px">Referred by:<span class="line"></span></div>

  <!-- allergies -->
  <span class="a h" style="left:30px;top:314px;font-size:9.6px">Please indicate if &nbsp;you are allergic to any of the following
    <svg class="tick" width="16" height="13" viewBox="0 0 16 13" aria-hidden="true"><rect x="0.5" y="2.5" width="11" height="10" fill="none" stroke="#333" stroke-width=".8"/><path d="M2 7l3 4L15 1" fill="none" stroke="#111" stroke-width="1.6"/></svg> ?</span>
  <span class="a sm" style="left:30px;top:335px">Aspirin</span><span class="abox" style="left:110px;top:336px"></span>
  <span class="a sm" style="left:130px;top:335px">Codeine</span><span class="abox" style="left:175px;top:336px"></span>
  <span class="a sm" style="left:195px;top:335px">Penicillin</span><span class="abox" style="left:243px;top:336px"></span>
  <span class="a sm" style="left:263px;top:335px">Sulfites</span><span class="abox" style="left:300px;top:336px"></span>
  <span class="a sm" style="left:30px;top:351px">Local Anaesthetic</span><span class="abox" style="left:110px;top:354px"></span>
  <span class="a sm" style="left:131px;top:351px">Lactose</span><span class="abox" style="left:175px;top:353px"></span>
  <span class="a sm" style="left:195px;top:351px">Nickel</span><span class="abox" style="left:243px;top:353px"></span>
  <span class="a sm" style="left:265px;top:351px">Latex</span><span class="abox" style="left:300px;top:353px"></span>
  <div class="field" style="left:30px;top:372px;width:419px">Other:<span class="line"></span></div>

  <!-- medications -->
  <span class="a h" style="left:30px;top:393px;font-size:9.6px">Are you currently taking, or have ever taken, any of the following medication
    <svg class="tick" width="16" height="13" viewBox="0 0 16 13" aria-hidden="true"><rect x="0.5" y="2.5" width="11" height="10" fill="none" stroke="#333" stroke-width=".8"/><path d="M2 7l3 4L15 1" fill="none" stroke="#111" stroke-width="1.6"/></svg> ?</span>

  <span class="a sm" style="left:29px;top:411px">Asthma inhaler</span><span class="abox" style="left:120px;top:411px"></span>
  <span class="a sm" style="left:146px;top:411px">Anti-epileptics</span><span class="abox" style="left:225px;top:411px"></span>
  <span class="a sm" style="left:259px;top:411px">Anti-depressants</span><span class="abox" style="left:342px;top:411px"></span>
  <span class="a sm" style="left:377px;top:411px">Blood Pressure</span><span class="abox" style="left:434px;top:412px"></span>

  <span class="a sm" style="left:29px;top:427px">Blood Thinners</span><span class="abox" style="left:120px;top:426px"></span>
  <span class="a sm" style="left:146px;top:427px">Bisphosphonates</span><span class="abox" style="left:225px;top:426px"></span>
  <span class="a sm" style="left:259px;top:427px">Chemotherapy</span><span class="abox" style="left:342px;top:426px"></span>
  <span class="a sm" style="left:377px;top:427px">Insulin</span><span class="abox" style="left:434px;top:427px"></span>

  <span class="a sm" style="left:29px;top:443px">Immunosuppressants</span><span class="abox" style="left:120px;top:442px"></span>
  <span class="a sm" style="left:146px;top:443px">Steroids</span><span class="abox" style="left:225px;top:442px"></span>
  <span class="a sm" style="left:259px;top:443px">Oral Contraceptive</span><span class="abox" style="left:342px;top:442px"></span>
  <span class="a sm" style="left:377px;top:443px">Other</span><span class="abox" style="left:434px;top:443px"></span>

  <span class="a h" style="left:29px;top:463px;font-size:9.4px">Please specify medication name, dose, and frequency where possible:</span>
  <div class="rule" style="left:30px;top:489px;width:130px"></div><div class="rule" style="left:174px;top:489px;width:128px"></div><div class="rule" style="left:317px;top:489px;width:128px"></div>
  <div class="rule" style="left:30px;top:506px;width:130px"></div><div class="rule" style="left:174px;top:506px;width:128px"></div><div class="rule" style="left:317px;top:506px;width:128px"></div>
  <div class="rule" style="left:30px;top:524px;width:130px"></div><div class="rule" style="left:174px;top:524px;width:128px"></div><div class="rule" style="left:317px;top:524px;width:128px"></div>

  <!-- other questions -->
  <span class="a h" style="left:30px;top:539px">Do you require antibiotic cover?</span>
  <span class="a" style="left:204px;top:539px">Yes</span><span class="abox" style="left:224px;top:539px"></span>
  <span class="a" style="left:241px;top:539px">No</span><span class="abox" style="left:258px;top:539px"></span>

  <span class="a h" style="left:30px;top:557px">Have you had a joint replacement?</span>
  <span class="a" style="left:204px;top:557px">Yes</span><span class="abox" style="left:224px;top:557px"></span>
  <span class="a" style="left:241px;top:557px">No</span><span class="abox" style="left:258px;top:557px"></span>

  <span class="a h" style="left:30px;top:580px">Women:</span>
  <span class="a h" style="left:30px;top:595px">Are you pregnant?</span>
  <span class="a" style="left:126px;top:595px">Yes</span><span class="abox" style="left:150px;top:595px"></span>
  <span class="a" style="left:171px;top:595px">No</span><span class="abox" style="left:190px;top:595px"></span>
  <span class="a" style="left:214px;top:595px">Possible</span><span class="abox" style="left:253px;top:595px"></span>
  <span class="a" style="left:274px;top:595px">or</span>
  <span class="a h" style="left:30px;top:610px">Breast Feeding?</span>
  <span class="a" style="left:126px;top:610px">Yes</span><span class="abox" style="left:150px;top:610px"></span>
  <span class="a" style="left:171px;top:610px">No</span><span class="abox" style="left:190px;top:610px"></span>

  <span class="turn">Please Turnover</span>

  <div class="band band--bottom"><span></span><span></span><span></span><span></span></div>
</section>

<section class="page page--two" aria-label="Page two: medical history">
  <div class="band band--top"><span></span><span></span><span></span><span></span></div>

  <div class="brand" style="left:30px;top:34px"><span>harbour dental</span><span class="brand__dot"></span></div>

  <p class="intro">Do you have, or have you had, any of the following?</p>

  <div class="section section--left" style="left:23px;top:100px">
    <div class="section__head">Dental</div>
    <div class="q"><span class="label">Acid Reflux</span><span>Yes</span><span class="box"></span><span>No</span><span class="box"></span></div>
    <div class="q"><span class="label">Bad Breath/Taste</span><span>Yes</span><span class="box"></span><span>No</span><span class="box"></span></div>
    <div class="q"><span class="label">Bleeding/Swollen/Sore Gums</span><span>Yes</span><span class="box"></span><span>No</span><span class="box"></span></div>
    <div class="q"><span class="label">Blisters/Ulcers in Mouth</span><span>Yes</span><span class="box"></span><span>No</span><span class="box"></span></div>
    <div class="q"><span class="label">Broken tooth/filling</span><span>Yes</span><span class="box"></span><span>No</span><span class="box"></span></div>
    <div class="q"><span class="label">Burning tongue</span><span>Yes</span><span class="box"></span><span>No</span><span class="box"></span></div>
    <div class="q"><span class="label">Dry mouth</span><span>Yes</span><span class="box"></span><span>No</span><span class="box"></span></div>
    <div class="q"><span class="label">Food collection between teeth</span><span>Yes</span><span class="box"></span><span>No</span><span class="box"></span></div>
    <div class="q"><span class="label">Grinding/clenching teeth (day/night)</span><span>Yes</span><span class="box"></span><span>No</span><span class="box"></span></div>
    <div class="q"><span class="label">Loose teeth</span><span>Yes</span><span class="box"></span><span>No</span><span class="box"></span></div>
    <div class="q"><span class="label">Crooked teeth</span><span>Yes</span><span class="box"></span><span>No</span><span class="box"></span></div>
    <div class="q"><span class="label">Discoloured teeth</span><span>Yes</span><span class="box"></span><span>No</span><span class="box"></span></div>
    <div class="q"><span class="label">Sensitivity to Hot/Cold</span><span>Yes</span><span class="box"></span><span>No</span><span class="box"></span></div>
    <div class="q"><span class="label">Tooth pain when chewing</span><span>Yes</span><span class="box"></span><span>No</span><span class="box"></span></div>
    <div class="q"><span class="label">Jaw pain/Fracture</span><span>Yes</span><span class="box"></span><span>No</span><span class="box"></span></div>
    <div class="q"><span class="label">Orthodontic treatment/history</span><span>Yes</span><span class="box"></span><span>No</span><span class="box"></span></div>
    <div class="q"><span class="label">Oral Cancer</span><span>Yes</span><span class="box"></span><span>No</span><span class="box"></span></div>
  </div>

  <div class="section section--left" style="left:23px;top:298px">
    <div class="section__head">Diet/Lifestyle</div>
    <div class="q q--tall"><span class="label">Drink more than one<br>glass alcohol per day</span><span>Yes</span><span class="box"></span><span>No</span><span class="box"></span></div>
    <div class="q"><span class="label">Smoking</span><span>Yes</span><span class="box"></span><span>No</span><span class="box"></span></div>
    <div class="q"><span class="label">Carbonated drinks</span><span>Yes</span><span class="box"></span><span>No</span><span class="box"></span></div>
    <div class="q"><span class="label">Sugary foods</span><span>Yes</span><span class="box"></span><span>No</span><span class="box"></span></div>
  </div>

  <div class="section section--left" style="left:23px;top:370px">
    <div class="section__head">Blood</div>
    <div class="q"><span class="label">Anaemia</span><span>Yes</span><span class="box"></span><span>No</span><span class="box"></span></div>
    <div class="q"><span class="label">Blood clots</span><span>Yes</span><span class="box"></span><span>No</span><span class="box"></span></div>
    <div class="q"><span class="label">Leukemia</span><span>Yes</span><span class="box"></span><span>No</span><span class="box"></span></div>
    <div class="q"><span class="label">Low platelets</span><span>Yes</span><span class="box"></span><span>No</span><span class="box"></span></div>
    <div class="q"><span class="label">Lymphoma</span><span>Yes</span><span class="box"></span><span>No</span><span class="box"></span></div>
    <div class="q"><span class="label">Haemophelia</span><span>Yes</span><span class="box"></span><span>No</span><span class="box"></span></div>
  </div>

  <div class="section section--left" style="left:23px;top:454px">
    <div class="section__head">Chest</div>
    <div class="q"><span class="label">Bronchitis</span><span>Yes</span><span class="box"></span><span>No</span><span class="box"></span></div>
    <div class="q"><span class="label">Cystic Fibrosis</span><span>Yes</span><span class="box"></span><span>No</span><span class="box"></span></div>
    <div class="q"><span class="label">Emphysema</span><span>Yes</span><span class="box"></span><span>No</span><span class="box"></span></div>
    <div class="q"><span class="label">Pneumonia</span><span>Yes</span><span class="box"></span><span>No</span><span class="box"></span></div>
  </div>

  <div class="section section--left" style="left:23px;top:516px">
    <div class="section__head">Infectious Disease</div>
    <div class="q"><span class="label">Creutzfeldt-Jakob Disease</span><span>Yes</span><span class="box"></span><span>No</span><span class="box"></span></div>
    <div class="q"><span class="label">Hepatitis A,B,C,D</span><span>Yes</span><span class="box"></span><span>No</span><span class="box"></span></div>
    <div class="q"><span class="label">HIV/AIDS</span><span>Yes</span><span class="box"></span><span>No</span><span class="box"></span></div>
    <div class="q"><span class="label">Influenza</span><span>Yes</span><span class="box"></span><span>No</span><span class="box"></span></div>
    <div class="q"><span class="label">Shingles</span><span>Yes</span><span class="box"></span><span>No</span><span class="box"></span></div>
    <div class="q"><span class="label">Tuberculosis</span><span>Yes</span><span class="box"></span><span>No</span><span class="box"></span></div>
  </div>

  <div class="section section--right" style="left:271px;top:102px">
    <div class="section__head">Heart</div>
    <div class="q"><span class="label">Angina</span><span>Yes</span><span class="box"></span><span>No</span><span class="box"></span></div>
    <div class="q"><span class="label">Atrial Fibrillation</span><span>Yes</span><span class="box"></span><span>No</span><span class="box"></span></div>
    <div class="q"><span class="label">Blood Pressure (High/Low)</span><span>Yes</span><span class="box"></span><span>No</span><span class="box"></span></div>
    <div class="q"><span class="label">Congenital Heart Disease</span><span>Yes</span><span class="box"></span><span>No</span><span class="box"></span></div>
    <div class="q"><span class="label">Heart attack</span><span>Yes</span><span class="box"></span><span>No</span><span class="box"></span></div>
    <div class="q"><span class="label">Heart murmur</span><span>Yes</span><span class="box"></span><span>No</span><span class="box"></span></div>
    <div class="q"><span class="label">Heart surgery</span><span>Yes</span><span class="box"></span><span>No</span><span class="box"></span></div>
    <div class="q"><span class="label">Heart valve replacement</span><span>Yes</span><span class="box"></span><span>No</span><span class="box"></span></div>
    <div class="q"><span class="label">Infective endocarditis</span><span>Yes</span><span class="box"></span><span>No</span><span class="box"></span></div>
    <div class="q"><span class="label">Rheumatic Heart Disease</span><span>Yes</span><span class="box"></span><span>No</span><span class="box"></span></div>
    <div class="q"><span class="label">Pacemaker</span><span>Yes</span><span class="box"></span><span>No</span><span class="box"></span></div>
    <div class="q"><span class="label">Stent</span><span>Yes</span><span class="box"></span><span>No</span><span class="box"></span></div>
  </div>

  <div class="section section--right" style="left:271px;top:250px">
    <div class="section__head">Other</div>
    <div class="q"><span class="label">Anxiety/PTSD</span><span>Yes</span><span class="box"></span><span>No</span><span class="box"></span></div>
    <div class="q"><span class="label">Arthritis</span><span>Yes</span><span class="box"></span><span>No</span><span class="box"></span></div>
    <div class="q"><span class="label">Alzheimer's</span><span>Yes</span><span class="box"></span><span>No</span><span class="box"></span></div>
    <div class="q"><span class="label">Asthma</span><span>Yes</span><span class="box"></span><span>No</span><span class="box"></span></div>
    <div class="q"><span class="label">Anaphylaxis</span><span>Yes</span><span class="box"></span><span>No</span><span class="box"></span></div>
    <div class="q"><span class="label">Auto-immune disease</span><span>Yes</span><span class="box"></span><span>No</span><span class="box"></span></div>
    <div class="q"><span class="label">Coeliac</span><span>Yes</span><span class="box"></span><span>No</span><span class="box"></span></div>
    <div class="q"><span class="label">Depression</span><span>Yes</span><span class="box"></span><span>No</span><span class="box"></span></div>
    <div class="q"><span class="label">Diabetes</span><span>Yes</span><span class="box"></span><span>No</span><span class="box"></span></div>
    <div class="q"><span class="label">Epilepsy</span><span>Yes</span><span class="box"></span><span>No</span><span class="box"></span></div>
    <div class="q"><span class="label">Kidney Disease</span><span>Yes</span><span class="box"></span><span>No</span><span class="box"></span></div>
    <div class="q"><span class="label">Liver Disease</span><span>Yes</span><span class="box"></span><span>No</span><span class="box"></span></div>
    <div class="q"><span class="label">Osteoporosis</span><span>Yes</span><span class="box"></span><span>No</span><span class="box"></span></div>
    <div class="q"><span class="label">Parkinson's</span><span>Yes</span><span class="box"></span><span>No</span><span class="box"></span></div>
    <div class="q"><span class="label">Radiation to Head/Neck</span><span>Yes</span><span class="box"></span><span>No</span><span class="box"></span></div>
    <div class="q"><span class="label">Schizophrenia</span><span>Yes</span><span class="box"></span><span>No</span><span class="box"></span></div>
    <div class="q"><span class="label">Snoring</span><span>Yes</span><span class="box"></span><span>No</span><span class="box"></span></div>
    <div class="q"><span class="label">Sleep apnea</span><span>Yes</span><span class="box"></span><span>No</span><span class="box"></span></div>
    <div class="q"><span class="label">Stroke</span><span>Yes</span><span class="box"></span><span>No</span><span class="box"></span></div>
  </div>

  <div class="field" style="left:271px;top:482px;width:186px;font-size:8.2px">Other:<span class="line"></span></div>

  <div class="field" style="left:20px;top:608px;width:251px;font-size:7.4px">Signature:<span class="line"></span></div>
  <div class="field" style="left:315px;top:608px;width:142px;font-size:7.4px">Date:<span class="line"></span></div>

  <p class="footer">Thank you for the time to complete your medical history form.<br>Oral health is linked to overall health and this comprehensive questionnaire will help us<br>to provide you with optimal and safe care.</p>

  <div class="band band--bottom"><span></span><span></span><span></span><span></span></div>
</section>

</body>
</html>
```